New business card for a regional office of a US M&A company

We need business card for a finance company, office based in Hong Kong , our Head office is in US, our business is to Merge and acquires companies , the new office will be a regional office for the Asia Pacific region. We want to use the head office logo as attached ( but don't have to be exactly the same, can be a variation to it) as a base and then add Asia Pacific alongside the logo.
We would prefer to have be bilingual Eng + Chinese, although we don't really have Chinese company name .

Industry/Entity Type

Business

Contact Information for Business Card

Clara Jo Tsang
 

VP,
APAC M&A Operations
Orin Vantage Asia Pacific Limited
 
Unit 1407, K18
18 Tai Lok Shan Road, 
Hong Kong 
 
M: +852 6038 1742
T : +852 2836 4100
F : +852 2836 4177
VOIP: 4158
 
cjtsang@orinvantage.com

Font styles to use
Serif
Sans Serif

Colors

Designer to choose colors to be used in the design.

Requirements
Must have
• APAC Office

```html
<!DOCTYPE html>
<html lang="en">
<head>
<meta charset="utf-8">
<title>Orin Vantage APAC Business Card</title>
<link rel="stylesheet" href="https://fonts.googleapis.com/css2?family=Montserrat:wght@400;500;600;700&family=Noto+Serif+TC:wght@400&display=swap">
<style>
  :root {
    --stage: #2b2b2d;
    --paper: #f3f4f5;
    --paper-edge: #e3e5e7;
    --navy: #13294a;
    --band: #1a2457;
    --cyan: #2aa7d4;
    --ink: #3a3d42;
    --map: #dfe2e6;
  }
  * { box-sizing: border-box; margin: 0; padding: 0; }
  html, body { width: 1200px; height: 834px; overflow: hidden; background: var(--stage); }
  .stage {
    width: 1200px; height: 834px;
    display: flex; align-items: center; justify-content: center; gap: 40px;
  }
  .card {
    position: relative; width: 540px; height: 310px;
    background: linear-gradient(135deg, #fafbfb 0%, var(--paper) 60%, var(--paper-edge) 100%);
    overflow: hidden;
    box-shadow: 0 10px 30px rgba(0,0,0,.45);
    font-family: "Montserrat", sans-serif;
  }
  .world-map {
    position: absolute;
    background: linear-gradient(120deg, var(--map), rgba(223,226,230,.35));
    border-radius: 40px 90px 60px 120px;
  }
  .card--back .world-map { left: 40px; top: 60px; width: 430px; height: 210px; }
  .card--front .world-map { left: 20px; top: 40px; width: 330px; height: 200px; }

  .top-tab {
    position: absolute; top: 0; left: 300px; width: 120px; height: 16px;
    background: var(--navy); border-bottom: 3px solid var(--cyan);
  }
  .brand-box {
    position: absolute; background: var(--navy);
    border-bottom: 4px solid var(--cyan);
    display: flex; flex-direction: column; align-items: center; justify-content: center; gap: 10px;
  }
  .card--back .brand-box { right: 30px; bottom: 50px; width: 190px; height: 96px; }
  .card--front .brand-box { left: 60px; top: 110px; width: 200px; height: 104px; }
  .brand-mark {
    width: 22px; height: 22px; border: 2px solid #e9edf2;
  }
  .brand-name {
    color: var(--cyan); font-weight: 700; font-size: 19px; letter-spacing: .5px;
  }

  .details {
    position: absolute; left: 300px; top: 30px; width: 230px; color: var(--ink);
  }
  .person-name {
    font-family: "Noto Serif TC", serif; font-size: 14px; color: #555;
  }
  .person-title { color: var(--cyan); font-size: 10px; margin-top: 3px; }
  .company { color: var(--cyan); font-weight: 700; font-size: 10.5px; margin-top: 14px; }
  .address { font-size: 10px; line-height: 1.35; margin-top: 2px; }
  .contacts { list-style: none; margin-top: 14px; font-size: 10px; line-height: 1.5; }
  .contacts li { display: flex; align-items: center; gap: 8px; }
  .contacts svg { width: 10px; height: 10px; flex: none; }

  .footer-band {
    position: absolute; left: 0; right: 0; bottom: 12px; height: 44px;
    background: var(--band);
    display: flex; align-items: center; justify-content: center;
  }
  .tagline { color: var(--cyan); font-size: 12px; font-weight: 600; }
</style>
</head>
<body>
<main class="stage">
  <section class="card card--back">
    <div class="world-map" role="img" aria-label="Faint dotted world map centred on Asia Pacific"></div>
    <div class="top-tab"></div>
    <div class="brand-box">
      <span class="brand-mark"></span>
      <span class="brand-name">ORIN VANTAGE</span>
    </div>
  </section>

  <section class="card card--front">
    <div class="world-map" role="img" aria-label="Faint dotted world map centred on Asia Pacific"></div>
    <div class="brand-box">
      <span class="brand-mark"></span>
      <span class="brand-name">ORIN VANTAGE</span>
    </div>
    <div class="details">
      <p class="person-name">Clara Jo Tsang 曾嘉柔</p>
      <p class="person-title">VP, APAC M&amp;A Operations</p>
      <p class="company">Orin Vantage Asia Pacific Limited</p>
      <p class="address">Unit 1407, K18<br>18 Tai Lok Shan Road,<br>Hong Kong</p>
      <ul class="contacts">
        <li><svg viewBox="0 0 10 10"><rect x="2.5" y="0.5" width="5" height="9" rx="1" fill="none" stroke="#2aa7d4"/></svg>+852 6038 1742</li>
        <li><svg viewBox="0 0 10 10"><path d="M2 1l2 2-1 1.5c.7 1.3 1.2 1.8 2.5 2.5L7 6l2 2-1.5 1.5C4 9 1 6 .5 2.5z" fill="none" stroke="#2aa7d4" stroke-width=".9"/></svg>+852 2836 4100</li>
        <li><svg viewBox="0 0 10 10"><rect x="1" y="4" width="8" height="4" fill="none" stroke="#2aa7d4"/><rect x="3" y="1" width="4" height="3" fill="none" stroke="#2aa7d4"/></svg>+852 2836 4177</li>
        <li><svg viewBox="0 0 10 10"><circle cx="5" cy="5" r="4.3" fill="none" stroke="#2aa7d4" stroke-width=".9"/><path d="M.7 5h8.6M5 .7c-2.2 2.5-2.2 6.1 0 8.6M5 .7c2.2 2.5 2.2 6.1 0 8.6" fill="none" stroke="#2aa7d4" stroke-width=".7"/></svg>www.orinvantage.com</li>
      </ul>
    </div>
    <div class="footer-band">
      <p class="tagline">Let’s create success together</p>
    </div>
  </section>
</main>
</body>
</html>
```